Design logo, business cards, and web page for new web and bi development consulting company

I've started a Web and Business Intelligence development consulting company. We develop on Quordex's stack, Visual Sudio and Tabula Server. We develop responsive web sites and business intelligence platforms. I plan on focusing on small to medium sized business as my client base. I need a logo, business cards, and a one page web site. We will do more with the web site with you in the next six months if the business survives. The name of the company is Corvalo Integration Solutions, Corvalo for short.

Target Market(s)

small to medium sized businesses

Industry/Entity Type

Business

Contact Information for Business Card

logo
name
title
email
phone

Logo Text

Corvalo Integration Solutions - web and data solutions

Coding

Coded - Design and coding required

Number of Pages Required

1 page

Font styles to use
Sans Serif

Colors
0355a3
0092cd
00a88f
6b449b

Requirements
Nice to have
• web and data solutions

```html
<!DOCTYPE html>
<html lang="en">
<head>
<meta charset="utf-8">
<title>Corvalo Integration Solutions</title>
<link href="https://fonts.googleapis.com/css2?family=Lato:ital,wght@0,300;0,400;0,700;0,900;1,300&display=swap" rel="stylesheet">
<style>
  :root{
    --navy:#1a3a8c;
    --blue:#0a3d8f;
    --sky:#0e7fcc;
    --teal:#1a9a7e;
    --grey-bg:#f4f4f4;
    --text:#444;
    --white:#fff;
    --contact-bg:#0b3e96;
  }
  *{box-sizing:border-box;margin:0;padding:0}
  html,body{width:693px;height:1200px;overflow:hidden;background:var(--white)}
  body{font-family:'Lato',sans-serif;color:var(--text);position:relative}

  .site-header{height:57px;position:relative}
  .brand{position:absolute;left:45px;top:10px}
  .brand-name{font-weight:900;font-size:25px;letter-spacing:1px;color:var(--navy);line-height:1}
  .brand-tag{font-weight:700;font-size:9px;color:var(--teal);margin-top:3px}
  .social{display:flex;gap:5px}
  .social span{width:15px;height:15px;border-radius:50%;display:block}
  .social .s1{background:#f0a030}.social .s2{background:#3b5ba8}.social .s3{background:#3fa7dc}
  .social .s4{background:#e07ab8}.social .s5{background:#c8282e}
  .site-header .social{position:absolute;right:53px;top:18px}

  .hero{position:absolute;left:0;top:57px;width:693px;height:285px;
    background:linear-gradient(180deg,#4e2c7e 0%,#6a4a9c 55%,#5d3c8e 100%);text-align:center;color:var(--white)}
  .main-nav{position:absolute;left:58px;top:0;width:576px;height:28px;background:var(--teal);display:flex;align-items:center;padding-left:19px}
  .main-nav a{color:var(--white);font-size:9.5px;text-decoration:none;margin-right:20px}
  .nav-search{position:absolute;right:8px;top:0;width:26px;height:28px;background:var(--white);display:flex;align-items:center;justify-content:center}
  .hero h1{position:absolute;top:110px;width:100%;font-weight:300;font-size:25px}
  .hero h1 b{font-weight:700}
  .hero p{position:absolute;top:151px;width:100%;font-style:italic;font-weight:300;font-size:17.5px;opacity:.9}
  .btn-start{position:absolute;left:294px;top:189px;width:105px;height:25px;background:var(--sky);color:var(--white);font-size:7.5px;font-weight:700;display:flex;align-items:center;justify-content:center;border-radius:2px}
  .hero-dots{position:absolute;top:265px;left:331px;display:flex;gap:4px}
  .hero-dots i{width:7px;height:7px;border:1px solid rgba(255,255,255,.7);border-radius:50%;display:block}

  .features{position:absolute;top:342px;left:0;width:693px;height:196px;background:var(--grey-bg)}
  .feature{position:absolute;top:50px;width:130px;text-align:center}
  .feature svg{display:block;margin:0 auto 14px;height:32px}
  .feature h3{font-size:10px;font-weight:700;color:var(--teal);margin-bottom:6px}
  .feature p{font-size:7px;line-height:12.8px;color:#555}

  .works{position:absolute;top:538px;left:0;width:693px;text-align:center}
  .works h2{margin-top:19px;font-size:16px;font-weight:700;color:#3a3a3a}
  .works .lead{margin-top:9px;font-size:10.5px;font-weight:300;color:#666}
  .filters{margin-top:29px;display:flex;justify-content:center;gap:4px}
  .filters span{height:18px;padding:0 10px;background:var(--sky);color:var(--white);font-size:6.5px;font-weight:700;display:flex;align-items:center;border-radius:1px}
  .filters .active{background:var(--blue)}
  .work-grid{position:absolute;left:51px;top:120px;display:grid;grid-template-columns:repeat(4,144px);grid-auto-rows:117px;gap:5.5px 5px}
  .work-grid div{width:144px;height:117px}

  .contact{position:absolute;top:1032px;left:0;width:693px;height:140px;background:var(--contact-bg);text-align:center;color:var(--white)}
  .contact h2{margin-top:20px;font-size:16px;font-weight:700}
  .contact .lead{margin-top:9px;font-size:10px;font-weight:300;color:#7f9ccc}
  .contact-line{margin-top:10px;font-size:7px;color:#cfd9ee;display:flex;justify-content:center;gap:22px}
  .contact-line span{display:flex;align-items:center;gap:5px}
  .contact .social{justify-content:center;margin-top:13px}

  .site-footer{position:absolute;top:1172px;left:0;width:693px;height:28px;background:var(--teal);color:#e6f5f1;font-size:7px;display:flex;align-items:center;justify-content:center}
</style>
</head>
<body>

<header class="site-header">
  <div class="brand">
    <div class="brand-name">CORVALO</div>
    <div class="brand-tag">Corvalo Integration Solutions</div>
  </div>
  <div class="social" aria-label="Social links"><span class="s1"></span><span class="s2"></span><span class="s3"></span><span class="s4"></span><span class="s5"></span></div>
</header>

<section class="hero" role="img" aria-label="City skyline at dusk with purple overlay">
  <nav class="main-nav">
    <a>Home</a><a>About Us</a><a>Services</a><a>Testimonials</a><a>News</a><a>Contact Us</a>
    <div class="nav-search">
      <svg width="12" height="12" viewBox="0 0 12 12"><circle cx="5" cy="5" r="3.8" fill="none" stroke="#999" stroke-width="1.6"/><line x1="7.8" y1="7.8" x2="11" y2="11" stroke="#999" stroke-width="1.8"/></svg>
    </div>
  </nav>
  <h1>We are <b>Web Business Intelligence</b></h1>
  <p>We also develop responsive web sites and business intelligence platforms.</p>
  <div class="btn-start">GET STARTED NOW</div>
  <div class="hero-dots"><i></i><i></i><i></i></div>
</section>

<section class="features">
  <div class="feature" style="left:49px">
    <svg viewBox="0 0 34 34" width="32"><rect x="2" y="2" width="30" height="30" fill="#1a9a7e"/></svg>
    <h3>Quordex's stack</h3>
    <p>Vestibulum id ligula porta euismod semper. Aenean lacinia bibendum nulla sed consectetur dui.</p>
  </div>
  <div class="feature" style="left:197px">
    <svg viewBox="0 0 34 34" width="32"><circle cx="17" cy="17" r="15" fill="#1a9a7e"/></svg>
    <h3>Vantix Studio</h3>
    <p>Fusce dapibus, cursus commodo, tortor mauris condimentum nibh, ut fermentum massa justo risus.</p>
  </div>
  <div class="feature" style="left:346px">
    <svg viewBox="0 0 34 30" width="36"><g fill="#1a9a7e"><rect x="0" y="0" width="34" height="6"/><rect x="0" y="8" width="34" height="6"/><rect x="0" y="16" width="34" height="6"/><rect x="0" y="24" width="34" height="6"/></g><g fill="#fff"><rect x="22" y="2" width="8" height="2"/><rect x="22" y="10" width="8" height="2"/><rect x="22" y="18" width="8" height="2"/><rect x="22" y="26" width="8" height="2"/></g></svg>
    <h3>Tabula Server</h3>
    <p>Aenean eu leo quam. Pellentesque ornare sem lacinia quam venenatis vestibulum sagittis lacus mollis.</p>
  </div>
  <div class="feature" style="left:508px">
    <svg viewBox="0 0 34 32" width="34"><rect x="1.5" y="1.5" width="31" height="21" fill="none" stroke="#1a9a7e" stroke-width="3"/><rect x="15" y="23" width="4" height="5" fill="#1a9a7e"/><rect x="9" y="28" width="16" height="3" fill="#1a9a7e"/></svg>
    <h3>Responsive web sites</h3>
    <p>Maecenas sed diam eget risus varius blandit sit amet non magna. Vivamus sagittis lacus vel augue laoreet.</p>
  </div>
</section>

<section class="works">
  <h2>Our Featured Works</h2>
  <p class="lead">Curabitur blandit tempus porttitor. Maecenas faucibus mollis interdum.</p>
  <div class="filters"><span class="active">ALL</span><span>DESIGNS</span><span>ILLUSTRATION</span><span>MOTION</span></div>
  <div class="work-grid">
    <div role="img" aria-label="Light bulb infographic illustration" style="background:linear-gradient(#a8dcdc,#7ec3c8)"></div>
    <div role="img" aria-label="Team working over documents and tablet" style="background:linear-gradient(135deg,#6e7a80,#c9ccd0)"></div>
    <div role="img" aria-label="Hand sketching a web page wireframe" style="background:#f3f3f3"></div>
    <div role="img" aria-label="Colourful chat bubbles illustration" style="background:linear-gradient(135deg,#f2f2f2,#e9c9d8)"></div>
    <div role="img" aria-label="Tiled app interface mockup" style="background:linear-gradient(135deg,#16355a,#2a6a92)"></div>
    <div role="img" aria-label="SEO concept illustration" style="background:linear-gradient(#f0ead6,#e0d8bf)"></div>
    <div role="img" aria-label="Sketched city with businesswoman" style="background:linear-gradient(#f2f2f2,#c9c9c9)"></div>
    <div role="img" aria-label="Devices showing charts illustration" style="background:linear-gradient(#cfd8e2,#9aa8b4)"></div>
    <div role="img" aria-label="Person peeking through torn paper" style="background:linear-gradient(135deg,#5a5550,#9a8a78)"></div>
    <div role="img" aria-label="Hands holding document and glasses illustration" style="background:#25a3b0"></div>
    <div role="img" aria-label="Hand holding phone over a magazine" style="background:linear-gradient(135deg,#d8d8d0,#4c7a2e)"></div>
    <div role="img" aria-label="Laptop with network icons illustration" style="background:#0f3d74"></div>
  </div>
</section>

<section class="contact">
  <h2>Get in Touch</h2>
  <p class="lead">Vestibulum id ligula porta felis euismod semper,malesuada euismod.</p>
  <div class="contact-line">
    <span><svg width="6" height="8" viewBox="0 0 6 8"><path d="M3 0a3 3 0 0 1 3 3c0 2-3 5-3 5S0 5 0 3a3 3 0 0 1 3-3z" fill="#e04848"/></svg>Harrow Lane No: 22/07 Brook City, Saturn</span>
    <span><svg width="8" height="7" viewBox="0 0 8 7"><path d="M0 2c0-1 1-2 4-2s4 1 4 2v1H6V2H2v1H0zM1.5 3h5l1 4h-7z" fill="#e04848"/></svg>0200 555 01 23</span>
  </div>
  <div class="social"><span class="s1"></span><span class="s2"></span><span class="s3"></span><span class="s4"></span><span class="s5"></span></div>
</section>

<footer class="site-footer">@ 2015 www.companyname.com . All Rights Reserved.</footer>

</body>
</html>
```